design a construction company business card

Design business card around our logo. Card must have all the typical info: name, title, address, phone, email, business name, etc. Somewhere on the card I would like to see our motto "Built on integrity... Inspired by commitment." Consider adding a splash of bright orange to the card to complement the blues and silvers/grays in the logo. We are open to metallic inks, textures, etc. We would like to see options on both light and dark backgrounds. The font in the logo is Euro Technic Extended Regular.

```html
<!DOCTYPE html>
<html lang="en">
<head>
<meta charset="utf-8">
<title>Harlow Contracting – Business Card</title>
<link rel="stylesheet" href="https://fonts.googleapis.com/css2?family=Poppins:wght@400;500;600;700&display=swap">
<style>
  :root {
    --backdrop: #e9e5e0;
    --steel-light: #dcdde0;
    --steel-mid: #c4c6ca;
    --steel-dark: #aeb1b5;
    --brand-blue: #2c3f9c;
    --accent-blue: #2f55d4;
    --ink-light: #ffffff;
    --ink-shadow: rgba(40, 44, 52, 0.55);
  }
  * { box-sizing: border-box; margin: 0; padding: 0; }
  html, body {
    width: 1200px;
    height: 1090px;
    overflow: hidden;
    background: var(--backdrop);
    font-family: "Poppins", sans-serif;
  }
  .card {
    position: absolute;
    left: 100px;
    top: 255px;
    width: 1000px;
    height: 580px;
    border-radius: 22px;
    overflow: hidden;
    background: linear-gradient(160deg, var(--steel-light) 0%, var(--steel-mid) 55%, var(--steel-dark) 100%);
    box-shadow: 0 18px 40px rgba(0,0,0,0.18);
  }
  .perforation-band {
    position: absolute;
    left: 10px;
    top: 10px;
    width: 980px;
    height: 150px;
    border-radius: 14px 14px 0 0;
    background: linear-gradient(180deg, #eef0f3 0%, #d7d9dc 100%);
  }
  .accent-bar {
    position: absolute;
    left: 0;
    top: 209px;
    width: 8px;
    height: 82px;
    background: var(--accent-blue);
  }
  .person-name {
    position: absolute;
    left: 57px;
    top: 212px;
    font-size: 31px;
    font-weight: 600;
    color: var(--brand-blue);
    letter-spacing: 0.5px;
  }
  .person-title {
    position: absolute;
    left: 57px;
    top: 258px;
    font-size: 22px;
    color: var(--ink-light);
    text-shadow: 0 1px 2px var(--ink-shadow);
  }
  .contact-list {
    position: absolute;
    left: 57px;
    top: 366px;
    list-style: none;
  }
  .contact-item {
    display: flex;
    align-items: center;
    height: 40px;
    font-size: 23px;
    color: var(--ink-light);
    text-shadow: 0 1px 2px var(--ink-shadow);
  }
  .contact-icon {
    width: 28px;
    height: 28px;
    margin-right: 16px;
    flex: none;
  }
  .web-domain { color: var(--brand-blue); text-shadow: none; }
  .company-name {
    position: absolute;
    right: 39px;
    top: 160px;
    text-align: right;
    font-size: 46px;
    font-weight: 600;
    line-height: 1.05;
    color: var(--brand-blue);
    letter-spacing: 2px;
  }
  .office {
    position: absolute;
    right: 39px;
    top: 405px;
    text-align: right;
  }
  .office-label {
    font-size: 21px;
    font-weight: 600;
    color: var(--brand-blue);
    margin-bottom: 8px;
  }
  .office-line {
    font-size: 21px;
    line-height: 40px;
    color: var(--ink-light);
    text-shadow: 0 1px 2px var(--ink-shadow);
  }
</style>
</head>
<body>
  <section class="card">
    <div class="perforation-band" role="img" aria-label="Perforated hexagon metal pattern band"></div>

    <div class="accent-bar"></div>
    <h1 class="person-name">DANA HOLLOWAY</h1>
    <p class="person-title">Director</p>

    <ul class="contact-list">
      <li class="contact-item">
        <svg class="contact-icon" viewBox="0 0 28 28" aria-hidden="true">
          <circle cx="14" cy="14" r="13" fill="var(--accent-blue)"/>
          <path d="M9 7.5l3 0 1.2 3.5-1.8 1.3a9 9 0 0 0 4.3 4.3l1.3-1.8 3.5 1.2 0 3a1.5 1.5 0 0 1-1.6 1.5A12 12 0 0 1 7.5 9.1 1.5 1.5 0 0 1 9 7.5z" fill="#fff"/>
        </svg>
        800-555-0142 (Toll free)
      </li>
      <li class="contact-item">
        <svg class="contact-icon" viewBox="0 0 28 28" aria-hidden="true">
          <circle cx="14" cy="14" r="13" fill="var(--accent-blue)"/>
          <rect x="10" y="6.5" width="8" height="15" rx="1.5" fill="none" stroke="#fff" stroke-width="1.6"/>
          <circle cx="14" cy="18.8" r="0.9" fill="#fff"/>
        </svg>
        253-555-0187
      </li>
      <li class="contact-item">
        <svg class="contact-icon" viewBox="0 0 28 28" aria-hidden="true">
          <circle cx="14" cy="14" r="13" fill="var(--accent-blue)"/>
          <rect x="7.5" y="9.5" width="13" height="9" fill="none" stroke="#fff" stroke-width="1.6"/>
          <path d="M7.5 9.5l6.5 5 6.5-5" fill="none" stroke="#fff" stroke-width="1.6"/>
        </svg>
        info@harlowcontracting.com
      </li>
      <li class="contact-item">
        <svg class="contact-icon" viewBox="0 0 28 28" aria-hidden="true">
          <circle cx="14" cy="14" r="13" fill="var(--accent-blue)"/>
          <circle cx="14" cy="14" r="7" fill="none" stroke="#fff" stroke-width="1.4"/>
          <ellipse cx="14" cy="14" rx="3" ry="7" fill="none" stroke="#fff" stroke-width="1.2"/>
          <path d="M7 14h14" stroke="#fff" stroke-width="1.2"/>
        </svg>
        www.<span class="web-domain">harlowcontracting</span>.com
      </li>
    </ul>

    <div class="company-name">HARLOW<br>CONTRACTING</div>

    <address class="office" style="font-style: normal;">
      <p class="office-label">HARLOWCONTRACTING</p>
      <p class="office-line">1180 Cedar Avenue NE</p>
      <p class="office-line">Suite #204 Sumner, WA 98390</p>
    </address>
  </section>
</body>
</html>
```